TALMORK

The business want a professional looking business card. We have a scetch we will add but want the extra upgrade, and would like more suggestions for variations of our business cards.

```html
<!DOCTYPE html>
<html lang="en">
<head>
<meta charset="utf-8">
<title>TALMORK – Business Card</title>
<link href="https://fonts.googleapis.com/css2?family=Playfair+Display:wght@700&family=Open+Sans:wght@400&display=swap" rel="stylesheet">
<style>
  :root {
    --backdrop: #8e8e8e;
    --card: #1e1e1e;
    --gold: #c9a13b;
    --ink-light: #e6e6e6;
  }
  * { margin: 0; padding: 0; box-sizing: border-box; }
  html, body {
    width: 1200px; height: 1200px; overflow: hidden;
    background: var(--backdrop);
  }
  .stage { position: relative; width: 1200px; height: 1200px; }
  .card {
    position: absolute; left: 281px; width: 642px; height: 366px;
    background: var(--card); border-radius: 24px;
  }
  .card--front { top: 195px; }
  .card--back { top: 639px; }

  .brand { position: absolute; text-align: center; transform: translateX(-50%); }
  .brand__dot { display: block; margin: 0 auto; border-radius: 50%; background: var(--gold); }
  .brand__name {
    font-family: "Playfair Display", serif; font-weight: 700; color: var(--gold);
    line-height: 1; white-space: nowrap;
  }
  .brand__since {
    font-family: "Open Sans", sans-serif; color: var(--ink-light);
    line-height: 1; white-space: nowrap;
  }

  .card--front .brand { left: 147px; top: 128px; }
  .card--front .brand__dot { width: 36px; height: 36px; margin-bottom: 48px; }
  .card--front .brand__name { font-size: 25px; letter-spacing: 7px; margin-right: -7px; }
  .card--front .brand__since { font-size: 9.5px; letter-spacing: 3.5px; margin-top: 8px; margin-right: -3.5px; }

  .card--back .brand { left: 321px; top: 122px; }
  .card--back .brand__dot { width: 56px; height: 56px; margin-bottom: 60px; }
  .card--back .brand__name { font-size: 38px; letter-spacing: 12px; margin-right: -12px; }
  .card--back .brand__since { font-size: 13.5px; letter-spacing: 6px; margin-top: 12px; margin-right: -6px; }

  .divider {
    position: absolute; left: 265px; top: 115px; width: 1.5px; height: 137px;
    background: var(--gold);
  }
  .person { position: absolute; left: 299px; top: 110px; }
  .person__name {
    font-family: "Playfair Display", serif; font-weight: 700; font-size: 27px;
    color: var(--gold); line-height: 1.1; white-space: nowrap;
  }
  .person__role {
    font-family: "Open Sans", sans-serif; font-size: 16px; color: var(--ink-light);
    margin-top: 3px;
  }
  .person__rule { width: 24px; height: 1.5px; background: var(--gold); margin-top: 14px; }

  .contacts { list-style: none; margin-top: 14px; }
  .contacts li {
    display: flex; align-items: center; height: 23px;
    font-family: "Open Sans", sans-serif; font-size: 14px; color: var(--ink-light);
  }
  .contacts svg { width: 12px; height: 12px; margin-right: 11px; flex: none; }
</style>
</head>
<body>
<div class="stage">

  <section class="card card--front">
    <div class="brand">
      <span class="brand__dot"></span>
      <div class="brand__name">TALMORK</div>
      <div class="brand__since">SINCE 2026</div>
    </div>

    <div class="divider"></div>

    <div class="person">
      <div class="person__name">Sven Aril Dahlberg</div>
      <div class="person__role">CEO &amp; Founder</div>
      <div class="person__rule"></div>
      <ul class="contacts">
        <li>
          <svg viewBox="0 0 24 24" aria-hidden="true"><path fill="var(--gold)" d="M6.6 10.8a15.1 15.1 0 0 0 6.6 6.6l2.2-2.2a1 1 0 0 1 1-.25 11.4 11.4 0 0 0 3.6.57 1 1 0 0 1 1 1V20a1 1 0 0 1-1 1A17 17 0 0 1 3 4a1 1 0 0 1 1-1h3.5a1 1 0 0 1 1 1c0 1.25.2 2.45.57 3.57a1 1 0 0 1-.25 1z"/></svg>
          004791234560
        </li>
        <li>
          <svg viewBox="0 0 24 24" aria-hidden="true"><rect x="2" y="5" width="20" height="14" rx="1.5" fill="var(--gold)"/><path d="M3 6.5l9 6.5 9-6.5" fill="none" stroke="var(--card)" stroke-width="1.8"/></svg>
          hello@talmork.com
        </li>
        <li>
          <svg viewBox="0 0 24 24" aria-hidden="true"><circle cx="12" cy="12" r="10" fill="none" stroke="var(--gold)" stroke-width="2.4"/><path d="M2 12h20M12 2c3 3 3 17 0 20M12 2c-3 3-3 17 0 20" fill="none" stroke="var(--gold)" stroke-width="1.6"/></svg>
          www.talmork.com
        </li>
      </ul>
    </div>
  </section>

  <section class="card card--back">
    <div class="brand">
      <span class="brand__dot"></span>
      <div class="brand__name">TALMORK</div>
      <div class="brand__since">SINCE 2026</div>
    </div>
  </section>

</div>
</body>
</html>
```